Willow Creek Gatherings Event Planning in need of a design!!

Event Planning company, does a variety of events. I like simple more rustic designs focused on almond blossoms. We are based out of Northern California, the heart of almond country. I would like to see colors in light pinks, beige, light browns, whites or creams. the final design should communicate rustic simplicity. Below are some pictures of Almond blossoms and design ideas I prefer the one called Tulip Grove. Thanks

Target Market(s)

Women in the mid twenties and older. They should be in the upper middle class in need of an amazing party design and coordinator

Industry/Entity Type

Event Planning

Contact Information for Business Card

Maren Lockwood 530-624-0295almondbaffairs@gmail.comalmondblossomaffairs.com

Font styles to use
Other font styles liked:
• Amatic SC

Requirements
Must have
• almond blossom
• my information
• simplicity
Nice to have
• rustic design
• vintage feel
• whimsical
Should not have
• i like pink but not over the top

```html
<!DOCTYPE html>
<html lang="en">
<head>
<meta charset="utf-8">
<title>Willow Creek Gatherings – Business Card</title>
<link rel="stylesheet" href="https://fonts.googleapis.com/css2?family=Jost:wght@400&family=Open+Sans:wght@400;700&display=swap">
<style>
  :root {
    --backdrop: #e4e3e1;
    --blossom-pink: #ec8fbb;
    --ink-black: #000000;
    --leaf-green: #2ea375;
    --paper-white: #ffffff;
  }
  * { margin: 0; padding: 0; box-sizing: border-box; }
  html, body {
    width: 1200px;
    height: 900px;
    overflow: hidden;
    background: var(--backdrop);
  }
  .canvas {
    position: relative;
    width: 1200px;
    height: 900px;
  }
  .card {
    position: absolute;
    left: 320px;
    width: 560px;
    height: 320px;
    overflow: hidden;
    box-shadow: 0 6px 18px rgba(0, 0, 0, 0.18);
  }
  .card--front {
    top: 100px;
    background: var(--blossom-pink);
    display: flex;
    align-items: center;
    justify-content: center;
  }
  .card--back {
    top: 480px;
    background: var(--blossom-pink);
  }
  .brand-name {
    font-family: "Jost", sans-serif;
    font-weight: 400;
    text-transform: uppercase;
    text-align: center;
    letter-spacing: 0.06em;
    line-height: 1.15;
  }
  .card--front .brand-name {
    color: var(--paper-white);
    font-size: 40px;
  }
  .back-shapes {
    position: absolute;
    inset: 0;
    width: 100%;
    height: 100%;
  }
  .back-shapes .panel-black { fill: var(--ink-black); }
  .back-shapes .panel-green { fill: var(--leaf-green); }
  .card--back .brand-name {
    position: absolute;
    left: 30px;
    top: 108px;
    width: 270px;
    color: var(--blossom-pink);
    font-size: 30px;
  }
  .contact {
    position: absolute;
    right: 24px;
    top: 150px;
    text-align: right;
    font-family: "Open Sans", sans-serif;
    color: var(--paper-white);
  }
  .contact__name {
    font-weight: 700;
    font-size: 18px;
    margin-bottom: 8px;
    margin-right: 22px;
  }
  .contact__line {
    display: flex;
    align-items: center;
    justify-content: flex-end;
    gap: 8px;
    font-size: 14px;
    line-height: 20px;
  }
  .contact__icon {
    width: 12px;
    height: 12px;
    flex: none;
  }
</style>
</head>
<body>
<main class="canvas">

  <section class="card card--front" aria-label="Business card front">
    <p class="brand-name">Willow Creek<br>Gatherings</p>
  </section>

  <section class="card card--back" aria-label="Business card back">
    <svg class="back-shapes" viewBox="0 0 560 320" preserveAspectRatio="none" aria-hidden="true">
      <path class="panel-green" d="M334 0 C372 120 322 262 214 320 H198 C302 252 352 120 318 0 Z"/>
      <path class="panel-black" d="M0 0 H320 C354 120 304 252 200 320 H0 Z"/>
    </svg>

    <p class="brand-name">Willow Creek<br>Gatherings</p>

    <div class="contact">
      <p class="contact__name">Maren Lockwood</p>
      <p class="contact__line">530-817-4362
        <svg class="contact__icon" viewBox="0 0 24 24" aria-hidden="true"><path fill="#fff" d="M6.6 10.8a15 15 0 0 0 6.6 6.6l2.2-2.2c.3-.3.7-.4 1-.2 1.1.4 2.3.6 3.6.6.6 0 1 .4 1 1V20c0 .6-.4 1-1 1A17 17 0 0 1 3 4c0-.6.4-1 1-1h3.5c.6 0 1 .4 1 1 0 1.3.2 2.5.6 3.6.1.3 0 .7-.2 1z"/></svg>
      </p>
      <p class="contact__line">willowcgather@mailbox.test
        <svg class="contact__icon" viewBox="0 0 24 24" aria-hidden="true"><rect x="2" y="5" width="20" height="14" rx="1.5" fill="none" stroke="#fff" stroke-width="2"/><path d="M3 6l9 7 9-7" fill="none" stroke="#fff" stroke-width="2"/></svg>
      </p>
      <p class="contact__line">willowcreekgatherings.test
        <svg class="contact__icon" viewBox="0 0 24 24" aria-hidden="true"><circle cx="12" cy="12" r="10" fill="none" stroke="#fff" stroke-width="2"/><path d="M2 12h20M12 2c3 3 3 17 0 20M12 2c-3 3-3 17 0 20" fill="none" stroke="#fff" stroke-width="1.6"/></svg>
      </p>
    </div>
  </section>

</main>
</body>
</html>
```